Grafic Ad for a Printmagazine about Tractor Vehicles

We need for a Geman Printmagazine about Tractors a Grafic Design in different sizes. Our Website and corporate Design: https://www.kalvimo.de You can work with the uploaded files . The round Logo with shaking hands should be included in your Designs somehow. Perhaps as a transparent in the background or placed in a corner. The Font used for the URL is Days (typelodge.com/days.font) Please use this Font or a other similar for the URL "kalvimo.de" and expand it to "www.kalvimo.de/traktorwert" For the other Text parts (first line) and (second line) you can use a other font which you prefer. We need the grafics as .jpg in the pixel sizes: 472x496, 437x614, 307x437 (Print would be DPI 300). Goal is a eye-catching design for the later print ad. Have fun and be creative ;)

Logo Text

"Traktor Bewertung" (first line), " Kurzgutachen für Verkauf, Kauf oder Versicherung" (second line), "www.kalvimo.de/traktorwert" (third line)

Logo styles of interest
Pictorial/Combination Logo
Font styles to use
Other font styles liked:
• Days.tff for the URL

Colors
0054AA
0677BA
7BADD7
CADEEF
E8F1F8
0094D4
00A9DD
6FCCEA
C7EBF8
E9F6FB

```html
<!DOCTYPE html>
<html lang="de">
<head>
<meta charset="utf-8">
<title>Traktor Bewertung – Anzeigen</title>
<link rel="stylesheet" href="https://fonts.googleapis.com/css2?family=Days+One&display=swap">
<style>
  :root {
    --page: #e8e8e8;
    --blue-deep: #0054AA;
    --blue: #0677BA;
    --blue-mid: #0094D4;
    --blue-bright: #00A9DD;
    --blue-soft: #6FCCEA;
    --blue-pale: #C7EBF8;
    --blue-mist: #E9F6FB;
    --grey-title: #555a5e;
    --brown: #3d2416;
    --white: #ffffff;
    --font: "Days One", "Trebuchet MS", sans-serif;
  }
  * { box-sizing: border-box; margin: 0; padding: 0; }
  html, body { width: 1200px; height: 2371px; overflow: hidden; }
  body { background: var(--page); position: relative; font-family: var(--font); }

  .ad {
    position: absolute;
    overflow: hidden;
    background: linear-gradient(180deg, var(--blue-mist) 0%, #b9e3f6 45%, #8fd0ef 100%);
  }
  .ad--wide   { left: 96px;  top: 94px;   width: 991px; height: 704px; }
  .ad--square { left: 192px; top: 882px;  width: 800px; height: 761px; }
  .ad--small  { left: 239px; top: 1734px; width: 705px; height: 496px; }

  .ad__waves { position: absolute; inset: 0; width: 100%; height: 100%; }
  .ad > * { position: absolute; }

  .brand__mark { border-radius: 50%; background: var(--blue-pale); border: 3px solid var(--blue-soft); }
  .brand__name { color: var(--blue); text-align: center; width: 240px; line-height: 1.1; }

  .stars { overflow: visible; }
  .title { white-space: nowrap; line-height: 1.1; color: var(--grey-title); font-weight: 400; }
  .title__accent { color: var(--blue); }

  .tractor-photo {
    border-radius: 40% 45% 30% 30%;
    background: radial-gradient(ellipse at 55% 45%, #7fb5df 0%, #4f8fc6 45%, rgba(60,90,120,0.55) 75%, rgba(60,90,120,0) 100%);
  }

  .url-pill {
    border-radius: 999px;
    background: linear-gradient(180deg, #5cb8ea 0%, var(--blue-mid) 45%, var(--blue) 100%);
    box-shadow: 4px 6px 8px rgba(0, 50, 90, 0.35), inset 0 2px 2px rgba(255,255,255,0.6);
    color: var(--white);
    display: flex; align-items: center; justify-content: center;
    white-space: nowrap;
  }

  .services__lead, .services__item { color: var(--brown); text-align: center; line-height: 1.2; white-space: nowrap; }
  .services__icon { color: var(--brown); }

  /* Wide */
  .ad--wide .brand__mark { left: 84px; top: 38px; width: 114px; height: 114px; }
  .ad--wide .brand__name { left: 30px; top: 161px; font-size: 26px; }
  .ad--wide .stars { left: 504px; top: 20px; width: 356px; height: 106px; }
  .ad--wide .title { left: 446px; top: 136px; font-size: 47px; }
  .ad--wide .tractor-photo { left: 156px; top: 272px; width: 396px; height: 306px; }
  .ad--wide .url-pill { left: 52px; top: 588px; width: 608px; height: 62px; font-size: 32px; }
  .ad--wide .services__lead, .ad--wide .services__item { left: 658px; width: 320px; }
  .ad--wide .services__lead { top: 256px; font-size: 22px; }
  .ad--wide .services__item { font-size: 30px; }
  .ad--wide .services__icon { left: 792px; width: 52px; height: 52px; }
  .ad--wide .i1 { top: 318px; } .ad--wide .t1 { top: 382px; }
  .ad--wide .i2 { top: 436px; } .ad--wide .t2 { top: 496px; }
  .ad--wide .i3 { top: 549px; } .ad--wide .t3 { top: 610px; }

  /* Square */
  .ad--square .brand__mark { left: 66px; top: 30px; width: 114px; height: 114px; }
  .ad--square .brand__name { left: 10px; top: 156px; font-size: 26px; }
  .ad--square .stars { left: 336px; top: 32px; width: 360px; height: 106px; }
  .ad--square .title { left: 282px; top: 148px; font-size: 46px; }
  .ad--square .tractor-photo { left: 66px; top: 318px; width: 408px; height: 312px; }
  .ad--square .url-pill { left: 40px; top: 658px; width: 460px; height: 46px; font-size: 26px; }
  .ad--square .services__lead, .ad--square .services__item { left: 473px; width: 300px; }
  .ad--square .services__lead { top: 293px; font-size: 24px; }
  .ad--square .services__item { font-size: 31px; }
  .ad--square .services__icon { left: 595px; width: 56px; height: 56px; }
  .ad--square .i1 { top: 360px; } .ad--square .t1 { top: 424px; }
  .ad--square .i2 { top: 482px; } .ad--square .t2 { top: 544px; }
  .ad--square .i3 { top: 600px; } .ad--square .t3 { top: 664px; }

  /* Small */
  .ad--small .brand__mark { left: 55px; top: 18px; width: 80px; height: 80px; }
  .ad--small .brand__name { left: -17px; top: 101px; font-size: 18px; }
  .ad--small .stars { left: 373px; top: 18px; width: 231px; height: 66px; }
  .ad--small .title { left: 335px; top: 92px; font-size: 30px; }
  .ad--small .tractor-photo { left: 49px; top: 192px; width: 291px; height: 222px; }
  .ad--small .url-pill { left: 30px; top: 422px; width: 364px; height: 38px; font-size: 20px; }
  .ad--small .services__lead { left: 386px; width: 280px; top: 174px; font-size: 21px; }
  .ad--small .services__item { left: 478px; text-align: left; font-size: 21px; }
  .ad--small .services__icon { left: 416px; width: 40px; height: 40px; }
  .ad--small .i1 { top: 242px; } .ad--small .t1 { top: 248px; }
  .ad--small .i2 { top: 332px; } .ad--small .t2 { top: 339px; }
  .ad--small .i3 { top: 424px; } .ad--small .t3 { top: 431px; }
</style>
</head>
<body>

<svg width="0" height="0" style="position:absolute" aria-hidden="true">
  <defs>
    <linearGradient id="star-fill" x1="0" y1="0" x2="0" y2="1">
      <stop offset="0" stop-color="#5fb6ec"/>
      <stop offset="1" stop-color="#1f7fcc"/>
    </linearGradient>
    <linearGradient id="band-fill" x1="0" y1="0" x2="1" y2="0">
      <stop offset="0" stop-color="#6FCCEA"/>
      <stop offset="1" stop-color="#C7EBF8"/>
    </linearGradient>
    <path id="star" d="M0,-1 L.265,-.364 L.951,-.309 L.428,.139 L.588,.809 L0,.45 L-.588,.809 L-.428,.139 L-.951,-.309 L-.265,-.364 Z" fill="url(#star-fill)" stroke="#2a86c8" stroke-width=".03"/>
    <g id="star-row">
      <use href="#star" transform="translate(30 58) scale(30)"/>
      <use href="#star" transform="translate(270 58) scale(30)"/>
      <use href="#star" transform="translate(88 52) scale(38)"/>
      <use href="#star" transform="translate(212 52) scale(38)"/>
      <use href="#star" transform="translate(150 46) scale(46)"/>
    </g>
    <g id="waves">
      <path d="M0,0 H1000 V235 C820,190 520,205 260,290 C170,300 70,300 0,290 Z" fill="#ffffff"/>
      <path d="M0,200 C80,255 200,278 330,284 C200,292 70,290 0,272 Z" fill="url(#band-fill)" opacity=".6"/>
      <path d="M640,238 C770,212 900,212 1000,228 V262 C900,242 780,236 640,238 Z" fill="#C7EBF8"/>
    </g>
    <g id="icon-tag" fill="none" stroke="currentColor" stroke-width="2.4" stroke-linejoin="round">
      <path d="M6,10 L30,4 L46,20 L28,46 L8,34 Z"/>
      <circle cx="34" cy="14" r="3"/>
      <path d="M14,26 L22,18 M14,19 l1,1 M21,25 l1,1"/>
      <path d="M22,34 L36,22"/>
    </g>
    <g id="icon-cash" fill="none" stroke="currentColor" stroke-width="2.4" stroke-linejoin="round" stroke-linecap="round">
      <rect x="4" y="18" width="32" height="20" rx="2"/>
      <circle cx="20" cy="28" r="5"/>
      <path d="M30,18 L40,10 H48 M36,18 L44,14"/>
    </g>
    <g id="icon-shield" fill="none" stroke="currentColor" stroke-width="2.4" stroke-linejoin="round" stroke-linecap="round">
      <path d="M26,4 L44,10 V24 C44,36 36,44 26,48 C16,44 8,36 8,24 V10 Z"/>
      <path d="M26,9 L39,14 V24 C39,33 33,39 26,42 C19,39 13,33 13,24 V14 Z"/>
      <path d="M19,26 L24,31 L33,21"/>
    </g>
  </defs>
</svg>

<!-- Wide format -->
<section class="ad ad--wide">
  <svg class="ad__waves" viewBox="0 0 1000 700" preserveAspectRatio="none" aria-hidden="true"><use href="#waves"/></svg>
  <div class="brand__mark"></div>
  <div class="brand__name">kalvimo.de</div>
  <svg class="stars" viewBox="0 0 300 90" aria-hidden="true"><use href="#star-row"/></svg>
  <h1 class="title">Traktor <span class="title__accent">Bewertung</span></h1>
  <div class="tractor-photo" role="img" aria-label="Foto eines blauen Oldtimer-Traktors"></div>
  <div class="url-pill">www.kalvimo.de/traktorwert</div>
  <p class="services__lead">Kurzgutachen für</p>
  <svg class="services__icon i1" viewBox="0 0 52 52" aria-hidden="true"><use href="#icon-tag"/></svg>
  <p class="services__item t1">Verkauf,</p>
  <svg class="services__icon i2" viewBox="0 0 52 52" aria-hidden="true"><use href="#icon-cash"/></svg>
  <p class="services__item t2">Kauf oder</p>
  <svg class="services__icon i3" viewBox="0 0 52 52" aria-hidden="true"><use href="#icon-shield"/></svg>
  <p class="services__item t3">Versicherung</p>
</section>

<!-- Square format -->
<section class="ad ad--square">
  <svg class="ad__waves" viewBox="0 0 1000 700" preserveAspectRatio="none" aria-hidden="true"><use href="#waves"/></svg>
  <div class="brand__mark"></div>
  <div class="brand__name">kalvimo.de</div>
  <svg class="stars" viewBox="0 0 300 90" aria-hidden="true"><use href="#star-row"/></svg>
  <h1 class="title">Traktor <span class="title__accent">Bewertung</span></h1>
  <div class="tractor-photo" role="img" aria-label="Foto eines blauen Oldtimer-Traktors"></div>
  <div class="url-pill">www.kalvimo.de/traktorwert</div>
  <p class="services__lead">Kurzgutachen für</p>
  <svg class="services__icon i1" viewBox="0 0 52 52" aria-hidden="true"><use href="#icon-tag"/></svg>
  <p class="services__item t1">Verkauf,</p>
  <svg class="services__icon i2" viewBox="0 0 52 52" aria-hidden="true"><use href="#icon-cash"/></svg>
  <p class="services__item t2">Kauf oder</p>
  <svg class="services__icon i3" viewBox="0 0 52 52" aria-hidden="true"><use href="#icon-shield"/></svg>
  <p class="services__item t3">Versicherung</p>
</section>

<!-- Small format -->
<section class="ad ad--small">
  <svg class="ad__waves" viewBox="0 0 1000 700" preserveAspectRatio="none" aria-hidden="true"><use href="#waves"/></svg>
  <div class="brand__mark"></div>
  <div class="brand__name">kalvimo.de</div>
  <svg class="stars" viewBox="0 0 300 90" aria-hidden="true"><use href="#star-row"/></svg>
  <h1 class="title">Traktor <span class="title__accent">Bewertung</span></h1>
  <div class="tractor-photo" role="img" aria-label="Foto eines blauen Oldtimer-Traktors"></div>
  <div class="url-pill">www.kalvimo.de/traktorwert</div>
  <p class="services__lead">Kurzgutachen für</p>
  <svg class="services__icon i1" viewBox="0 0 52 52" aria-hidden="true"><use href="#icon-tag"/></svg>
  <p class="services__item t1">Verkauf,</p>
  <svg class="services__icon i2" viewBox="0 0 52 52" aria-hidden="true"><use href="#icon-cash"/></svg>
  <p class="services__item t2">Kauf oder</p>
  <svg class="services__icon i3" viewBox="0 0 52 52" aria-hidden="true"><use href="#icon-shield"/></svg>
  <p class="services__item t3">Versicherung</p>
</section>

</body>
</html>
```